Medical Billing Company Needs a Business Card Design

We need a business card design for a Florida based medical billing company called 'Clinicians Keystone Solutions'. We specialize in providing revenue cycle management services to physician and therapist offices (we're basically their back-office processing partner for providing billing software, claims submissions, A/R follow-up and patient statements & collections. Our logo is red and blue-ish, so make sure that whatever other elements are used will match appropriately. Our current business card design has a too small font size. I'd like to project an image that shows we are modern & reliable. On a side note, I'm planning on using ZUB for printing these cards.

Target Market(s)

Office managers, physicians, therapists

Industry/Entity Type

Printing

Requirements
Must have
• Logo
Name of Employee
Phone
Fax
E-mail
Website

```html
<!DOCTYPE html>
<html lang="en">
<head>
<meta charset="utf-8">
<title>Clinicians Keystone Solutions – Business Card</title>
<link rel="stylesheet" href="https://fonts.googleapis.com/css2?family=Open+Sans:wght@400;600;700&display=swap">
<style>
  :root {
    --page-bg: #e9e7e4;
    --navy: #2b2f86;
    --crimson: #c0272d;
    --ink: #55575c;
    --rule: #3a3f8f;
    --metal-light: #f4f5f6;
    --metal-mid: #c9cbce;
    --metal-dark: #a9acb0;
  }
  * { box-sizing: border-box; margin: 0; padding: 0; }
  html, body { width: 1200px; height: 720px; overflow: hidden; }
  body {
    background: var(--page-bg);
    font-family: "Open Sans", sans-serif;
    color: var(--ink);
    display: flex;
    align-items: center;
    justify-content: center;
    gap: 40px;
  }
  .card {
    position: relative;
    width: 540px;
    height: 309px;
    border-radius: 4px;
    overflow: hidden;
    background:
      conic-gradient(from 20deg at 50% 45%,
        var(--metal-mid), var(--metal-light) 30deg, var(--metal-mid) 70deg,
        var(--metal-dark) 110deg, var(--metal-light) 160deg, var(--metal-mid) 200deg,
        var(--metal-light) 250deg, var(--metal-dark) 300deg, var(--metal-mid) 360deg);
    box-shadow: 0 2px 0 #9ea1a5, 0 4px 0 #b7babd, 0 10px 22px rgba(0,0,0,.22);
  }

  /* Front */
  .brand-name {
    position: absolute;
    left: 36px; top: 40px;
    font-size: 25px;
    font-weight: 400;
    letter-spacing: 2px;
    color: var(--navy);
  }
  .employee {
    position: absolute;
    left: 36px; top: 196px;
  }
  .employee-name { font-size: 17px; font-weight: 700; color: var(--navy); }
  .employee-title { font-size: 12px; font-weight: 600; color: var(--crimson); }
  .front-web {
    position: absolute;
    left: 36px; bottom: 24px;
    font-size: 13px;
    color: var(--ink);
  }
  .front-web .accent { color: var(--crimson); }
  .divider {
    position: absolute;
    left: 300px; top: 120px;
    width: 1.5px; height: 120px;
    background: var(--rule);
  }
  .contact {
    position: absolute;
    left: 316px; top: 124px;
    font-size: 12.5px;
    line-height: 1.45;
    color: var(--ink);
    list-style: none;
  }
  .contact li { display: flex; align-items: center; gap: 7px; }
  .contact svg { width: 11px; height: 11px; flex: none; }
  .address { margin-top: 8px; display: block; padding-left: 0; }

  /* Back */
  .back-brand {
    position: absolute;
    left: 0; right: 0; top: 112px;
    text-align: center;
    font-size: 28px;
    font-weight: 400;
    letter-spacing: 2px;
    color: var(--navy);
  }
  .back-web {
    position: absolute;
    right: 40px; bottom: 34px;
    font-size: 16px;
    letter-spacing: .5px;
    color: var(--ink);
  }
  .back-web .name { color: var(--navy); }
  .back-web .accent { color: var(--crimson); }
</style>
</head>
<body>

  <section class="card card-front" aria-label="Business card front">
    <div class="brand-name">CLINICIANS KEYSTONE</div>

    <div class="employee">
      <div class="employee-name">Your Name</div>
      <div class="employee-title">Title</div>
    </div>

    <div class="front-web">www.<span class="name">clinician</span><span class="accent">keystone</span>.com</div>

    <div class="divider"></div>

    <ul class="contact">
      <li>
        <svg viewBox="0 0 12 12" aria-hidden="true"><circle cx="6" cy="6" r="6" fill="var(--crimson)"/><path d="M4 3.2l1.2 1.4-.7.8c.4.9 1.1 1.6 2 2l.8-.7 1.4 1.2-.7 1c-2.4-.3-4.3-2.2-4.6-4.6z" fill="#fff"/></svg>
        123-456-0789
      </li>
      <li>
        <svg viewBox="0 0 12 12" aria-hidden="true"><rect x="2.5" y="1" width="7" height="4" fill="var(--crimson)"/><rect x="1" y="4.5" width="10" height="5" rx="1" fill="var(--crimson)"/><rect x="3.5" y="7.5" width="5" height="3.5" fill="#fff" stroke="var(--crimson)" stroke-width=".8"/></svg>
        123-456-0789
      </li>
      <li>
        <svg viewBox="0 0 12 12" aria-hidden="true"><circle cx="6" cy="6" r="6" fill="var(--crimson)"/><rect x="3" y="4" width="6" height="4.2" fill="#fff"/><path d="M3 4l3 2.3L9 4" fill="none" stroke="var(--crimson)" stroke-width=".7"/></svg>
        info@cliniciankeystone.com
      </li>
      <li class="address">Street Name, City Name<br>State Zip Code</li>
    </ul>
  </section>

  <section class="card card-back" aria-label="Business card back">
    <div class="back-brand">CLINICIANS KEYSTONE</div>
    <div class="back-web">www.<span class="name">clinician</span><span class="accent">keystone</span>.com</div>
  </section>

</body>
</html>
```